Hard-File Archival Services Billboard (Digitization Service) for Attorneys/Law Firms

I need a billboard design for my company "Velkor Legal Aides" that advertises our primary service: Digitization of closed client files, for law firms and attorneys. Our system works as follows: 1) We get a call about a firm that wants to digitize their archived (closed) client files (which usually find their way to file cabinets or bankers boxes), 2) We go and pick those up from the law firm, 3) We bring them to our digitization facility, scan them in, and convert them into searchable PDF/A files, and 4) We upload them on the cloud, give the client a URL to visit their files whenever they want, and we delete them when requested by the client (usually for the retention duration for Missouri's rules of professional conduct, which is 6 years). It would be really cool to see "Velkor Legal Aides" and the logo clearly on the billboard, some simple sentence relating to "Missouri's best digitizing and cloud storage service for closed client files for attorneys" (or something shorter, you get the point), with maybe a linear set of photos and arrows (as follows 1. A photo of a file cabinet opened with files hanging out of it, 2. an arrow pointing to a person scanning in documents in a big scanner (maybe with a Velkor Legal Aidez logo on it?), 3. An arrow pointing to a "secure" appearing cloud (representing cloud storage), and 4. the client sitting at a computer with an arrow pointing back to the cloud (showing the client is accessing the cloud files through the computer). Our website is www.velkorlegalaides.example if you want to glean any additional information from there. Thanks! Oh yes, I should also say the billboard dimensions (in the event you need this for photo aspect ratio) will be as follows: 14 feet tall by 48 feet wide.
Target Market(s)
Attorneys in Springfield, Missouri
Industry/Entity Type
Legal
Look and feel

```html
<!DOCTYPE html>
<html lang="en">
<head>
<meta charset="utf-8">
<title>Velkor Legal Aides – Digitize Billboard</title>
<link rel="stylesheet" href="https://fonts.googleapis.com/css2?family=Oswald:wght@500;600;700&display=swap">
<style>
  :root {
    --page-bg: #e6e8eb;
    --board-black: #161616;
    --board-glow: #2a2a2a;
    --ink-white: #f4f4f4;
    --accent-orange: #e8951f;
    --spine-band: #1a1a1a;
  }
  html, body {
    margin: 0;
    padding: 0;
    width: 1200px;
    height: 900px;
    overflow: hidden;
    background: var(--page-bg);
  }
  .canvas {
    position: relative;
    width: 1200px;
    height: 900px;
    display: flex;
    align-items: center;
    justify-content: center;
  }
  .billboard {
    width: 1100px;
    height: 325px;
    display: block;
    box-shadow: 0 10px 30px rgba(0,0,0,0.18);
  }
  .headline {
    font-family: "Oswald", sans-serif;
    font-weight: 700;
    fill: var(--ink-white);
  }
  .subline {
    font-family: "Oswald", sans-serif;
    font-weight: 600;
    fill: var(--ink-white);
  }
  .brand-name {
    font-family: "Oswald", sans-serif;
    font-weight: 600;
    fill: var(--ink-white);
  }
  .brand-tagline {
    font-family: "Oswald", sans-serif;
    font-weight: 600;
    fill: var(--accent-orange);
  }
</style>
</head>
<body>
<main class="canvas">
  <svg class="billboard" viewBox="0 0 1100 325" xmlns="http://www.w3.org/2000/svg" role="img" aria-label="Digitize closed client files with us – Velkor Legal Aides, for attorneys">
    <defs>
      <radialGradient id="board-light" cx="0.45" cy="0.3" r="0.8">
        <stop offset="0" stop-color="var(--board-glow)"/>
        <stop offset="1" stop-color="var(--board-black)"/>
      </radialGradient>
    </defs>

    <rect class="board-surface" x="0" y="0" width="1100" height="325" fill="url(#board-light)"/>

    <g class="headline-group">
      <text class="headline" x="56" y="213" font-size="190" textLength="255" lengthAdjust="spacingAndGlyphs">DIG</text>
      <g class="binder-spine">
        <polygon points="329,64 368,64 361,213 322,213" fill="var(--accent-orange)"/>
        <rect x="333" y="92" width="26" height="5" fill="var(--spine-band)"/>
        <rect x="327" y="188" width="26" height="5" fill="var(--spine-band)"/>
      </g>
      <text class="headline" x="367" y="213" font-size="190" textLength="292" lengthAdjust="spacingAndGlyphs">TIZE</text>
      <text class="subline" x="56" y="269" font-size="54" textLength="600" lengthAdjust="spacingAndGlyphs">CLOSED CLIENT FILES WITH US</text>
    </g>

    <g class="monitor">
      <rect x="698" y="62" width="333" height="182" fill="none" stroke="var(--ink-white)" stroke-width="8" rx="3"/>
      <rect x="818" y="248" width="81" height="21" fill="var(--ink-white)"/>
      <polygon points="770,271 954,271 962,291 762,291" fill="var(--accent-orange)"/>
    </g>

    <g class="brand-lockup">
      <circle cx="790" cy="150" r="26" fill="none" stroke="var(--ink-white)" stroke-width="5"/>
      <text class="brand-name" x="830" y="146" font-size="26" textLength="180" lengthAdjust="spacingAndGlyphs">VELKOR LEGAL AIDES</text>
      <text class="brand-tagline" x="830" y="178" font-size="26" textLength="140" lengthAdjust="spacingAndGlyphs">FOR ATTORNEYS</text>
    </g>
  </svg>
</main>
</body>
</html>
```